African homeware retailer needs a web page design

We need a web page design for a new homeware and accessories store based in Johannesburg, South Africa. Our store carries modern African inspired items from designers that support social development and poverty alleviation initiatives. We have a particular preference for outfits that are centred on the empowerment of women.

Our business celebrates the skill, design and product of African craft and the work of designers looking to take that forward in a socially beneficial way (creating employment, developing skills, supporting local crafts people etc). We aim to carry items and inspirations from all over the African continent.

We would like to see a design that communicates African beauty and elegance without the typical tribal references that are made in reference to African craft or art.

We would like the web page to be stylish, uncomplicated, modern, captivating and appealing to the discerning customer. A similar value proposition is that of http://www.marlowtenwick.example/.

This is an e-commerce website which must be attractive to both individual buyers and design professionals so the website needs to look professional.

Here are links to some websites we like:
http://www.quenbyhollis.example/
http://www.dravelo.example/

Our logo is attached to the brief.

Target Market(s)

Our target market is female, age 20-50. However should not alienate the design conscious male customer therefore

Industry/Entity Type

E-Commerce

Requirements
Must have
• - A featured product banner which includes a photograph and text. This should be easy to edit as we will be changing the featured product regularly
- An easily expendable products section with categories. Examples of categories could be cushions, bedding, crockery etc. Should be easy to add new categories as well as new product pictures
- Home/landing page should be uncluttered
- Should use the logo and should be easy to change the logo which we have in various colour combinations. We plan to change the logo colours depending on circumstance e.g. make it red and white around Valentines day (similar to the way Vintrel frequently changes the logo on their landing page)

```html
<!DOCTYPE html>
<html lang="en">
<head>
<meta charset="utf-8">
<title>Amara Home – home care &amp; accessories</title>
<link href="https://fonts.googleapis.com/css2?family=Arimo:wght@400;700&family=Dosis:wght@400;500;600&display=swap" rel="stylesheet">
<style>
:root{
  --orange:#e2501c;
  --teal:#4f9a96;
  --teal-dark:#217b74;
  --ink:#333;
  --muted:#666;
  --dark:#2b2b2b;
  --line:#e2e2e2;
  --page:#f5f5f5;
  --card:#c9c9c9;
  --caption:#6a6a6a;
  --white:#fff;
}
*{box-sizing:border-box;margin:0;padding:0}
html,body{width:679px;height:1200px;overflow:hidden}
body{position:relative;background:var(--page);font-family:Arimo,Arial,sans-serif;color:var(--ink)}
.abs{position:absolute}
/* header */
.brand{left:58px;top:30px;width:86px;text-align:center}
.brand-mark{display:block;width:14px;height:14px;margin:0 auto 6px;background:var(--orange)}
.brand-name{font-size:15px;font-weight:700;color:var(--orange);letter-spacing:1px;line-height:1.1}
.tagline{left:212px;top:42px;font-family:Dosis,sans-serif;font-size:19px;color:var(--teal-dark);font-weight:500}
.tagline b{display:inline-block;width:16px;height:16px;border-radius:50%;background:var(--teal-dark);color:#fff;font-size:11px;text-align:center;line-height:16px;vertical-align:2px}
.toplinks{left:481px;top:10px;font-size:7px;font-weight:700;color:#444}
.toplinks span{margin-right:6px}
.callus{left:542px;top:32px;font-size:10px;color:var(--teal-dark);line-height:1.1}
.callus strong{display:block;color:var(--orange);font-size:10px}
.callus svg{position:absolute;left:-10px;top:3px}
.site-search{left:478px;top:67px;width:144px;height:20px;background:#fff;border:1px solid #e6e6e6;font-size:7px;color:#aaa;padding:6px 7px;font-style:italic}
.site-search svg{position:absolute;right:6px;top:5px}
/* nav */
.nav{left:0;top:101px;width:679px;height:24px;background:var(--orange);display:flex;align-items:center;font-size:8.5px;color:#fff}
.nav a{position:absolute;color:#fff;text-decoration:none}
/* main panel */
.panel{left:56px;top:126px;width:567px;height:728px;background:#fff;box-shadow:0 1px 3px rgba(0,0,0,.2)}
.sidebar-head{left:56px;top:128px;width:124px;height:30px;background:var(--teal);color:#fff;font-weight:700;font-size:9.5px;text-align:center;line-height:30px;letter-spacing:.3px}
.cats{left:72px;top:172px;width:98px;font-size:6.2px;color:#444}
.cats li{list-style:none;position:relative;height:14.5px;line-height:11px}
.cats .sub{padding-left:25px}
.cats .top{padding-left:15px}
.cats .top::before{content:"★";position:absolute;left:2px;top:-1px;font-size:7px}
.cats .n{position:absolute;right:0;top:2px;width:15px;height:7px;background:#333;color:#fff;font-size:5px;line-height:7px;text-align:center}
.cats .n.hot{background:var(--orange)}
.cats .sub::before{content:"";position:absolute;left:6px;top:6px;width:10px;border-top:1px solid #ccc}
.week{left:56px;top:446px;width:124px;height:30px;background:var(--dark);color:#fff;font-size:8.5px;font-weight:700;line-height:30px;padding-left:10px}
.week-img{left:56px;top:478px;width:124px;height:113px;background:linear-gradient(135deg,#f4f4f4 10%,#c23a2c 35%,#f0c23a 50%,#1d4f6e 65%,#f4f4f4 92%)}
.news-title{left:63px;top:597px;font-size:25px;color:#111;letter-spacing:.5px}
.news-sub{left:63px;top:632px;font-size:9.5px;color:#111}
.news-item{left:63px;width:112px;font-size:7px;line-height:9.4px;color:#333}
.news-item .avatar{position:absolute;left:0;top:0;width:33px;height:34px;background:linear-gradient(#7e6a5c,#c9b3a1)}
.news-item .meta{margin-left:38px;font-size:7.5px;line-height:12px;font-weight:700;color:#111;height:42px}
.news-item .meta span{font-weight:400}
.dots{left:100px;top:816px;display:flex;gap:3px}
.dots i{width:4px;height:4px;border-radius:50%;background:#222}
.dots i.on{background:var(--orange)}
.share{left:56px;top:834px;width:124px;height:38px;background:var(--dark)}
.share span{position:absolute;top:10px;width:18px;height:18px;border:1.3px solid #fff;border-radius:50%}
/* content */
.prod-search{left:194px;top:138px;width:286px;height:21px;background:#f1f1f1;border:1px solid #e2e2e2;font-size:6.5px;color:#777;padding:7px 8px}
.prod-search svg{position:absolute;right:6px;top:4px}
.hero{left:181px;top:169px;width:442px;height:208px;background:linear-gradient(90deg,#1a1a1a 0%,#c3151a 20%,#9f1115 40%,#e9e6d6 62%,#f4f1e4 80%,#6b6b66 100%)}
.hero-dots{left:359px;top:365px;display:flex;gap:2px}
.hero-dots i{width:20px;height:3px;background:#6f8f8e}
.hero-dots i.on{background:var(--orange)}
.statement{left:190px;top:390px;width:424px;text-align:center;font-size:19.6px;line-height:25px;color:#444}
.section-label{left:181px;width:442px;height:22px;text-align:center;font-size:8px;color:var(--orange);border-bottom:2px solid #f0f0f0;line-height:14px}
.card{width:90px;height:134px;background:#fff;box-shadow:0 0 2px rgba(0,0,0,.2)}
.card .price{height:14px;font-size:6.8px;padding:3px 6px;color:#222;position:relative}
.card .price svg{position:absolute;right:5px;top:3px}
.card .photo{height:106px;background:var(--card)}
.card .cap{height:14px;background:var(--caption);color:#fff;font-size:7.5px;text-align:center;line-height:14px}
.arrow{width:12px;height:12px;border-radius:50%;background:#222}
.arrow svg{display:block}
.pager{left:341px;top:853px;display:flex;background:#fff;box-shadow:0 1px 2px rgba(0,0,0,.2)}
.pager span{width:20px;height:18px;font-size:7.5px;line-height:18px;text-align:center;border-right:1px solid #e6e6e6}
.pager .on{background:var(--orange);color:#fff}
/* categories */
.cat-title{left:0;top:894px;width:679px;text-align:center;font-family:Dosis,sans-serif;font-weight:600;font-size:14px;color:var(--orange)}
.cat-rule{left:56px;top:917px;width:566px;border-top:1px solid #d6d6d6}
.chip{width:112px;height:23px;background:#f3f3f3;border:1px solid #cfcfcf;box-shadow:0 1px 1px rgba(0,0,0,.1);font-family:Dosis,sans-serif;font-size:11.5px;color:#555;text-align:center;line-height:21px}
.chev{top:966px;font-size:20px;color:#bbb;font-family:Dosis,sans-serif}
/* footer */
.footer{left:0;top:1038px;width:679px;height:162px;background:#f0f0f0}
.fbrand{left:62px;top:1088px;width:104px;text-align:center}
.fbrand .brand-mark{width:22px;height:22px;margin-bottom:10px}
.fbrand .brand-name{font-size:17px}
.fhead{top:1054px;font-size:8px;font-weight:700;color:#222}
.flinks{left:205px;top:1072px;font-size:7.5px;line-height:13.3px;color:#333;list-style:none}
.field{left:335px;width:119px;height:14px;border:1px solid #bbb;background:#fff;font-size:6.5px;color:#777;padding:2px 5px;font-style:italic}
.submit{left:335px;top:1171px;width:40px;height:13px;background:var(--orange);color:#fff;font-size:7.5px;font-weight:700;text-align:center;line-height:13px}
.soc{width:20px;height:20px;background:#7a7a7a}
.pay{height:10px;width:22px;background:#dcdcdc;border:1px solid #c8c8c8}
.copy{left:488px;top:1178px;font-size:6.5px;color:#444}
</style>
</head>
<body>

<!-- header -->
<div class="abs brand"><span class="brand-mark"></span><div class="brand-name">AMARA HOME</div></div>
<div class="abs tagline">home care <b>&amp;</b> accessories</div>
<div class="abs toplinks"><span>Order Status | Help</span><span>&#128274; LOGIN / SIGN UP</span></div>
<div class="abs callus">
  <svg width="8" height="14" viewBox="0 0 8 14"><path d="M6 1 C1 1 0 4 0 7 C0 10 1 13 6 13 L7 10 L5 9.5 C3.5 10 3 8.5 3 7 C3 5.5 3.5 4 5 4.5 L7 4 Z" fill="#222"/></svg>
  Call us<strong>555-010-4729</strong>
</div>
<div class="abs site-search">Search Products
  <svg width="10" height="10" viewBox="0 0 10 10"><circle cx="6" cy="4" r="3" fill="none" stroke="#999"/><path d="M4 6 L1 9" stroke="#999"/></svg>
</div>

<nav class="abs nav">
  <a style="left:57px;font-weight:700">Shop Now</a>
  <a style="left:120px">Our Story</a>
  <a style="left:176px">Blog</a>
  <a style="left:214px">Custom Design</a>
  <a style="left:294px">Our Shop</a>
  <a style="left:351px">Press &amp; Mentions</a>
  <a style="left:444px">Designer &amp; Architects</a>
  <a style="left:550px">Video</a>
  <a style="left:590px">Contact</a>
</nav>

<!-- main panel -->
<div class="abs panel"></div>

<aside>
  <div class="abs sidebar-head">ALL CATEGORIES</div>
  <ul class="abs cats">
    <li class="top">ALL ARTS <span class="n">123</span></li>
    <li class="sub">Bedding <span class="n">25</span></li>
    <li class="sub">Wall <span class="n hot">13</span></li>
    <li class="sub">Decor <span class="n">31</span></li>
    <li class="sub">Watches <span class="n">13</span></li>
    <li class="sub">Chairs <span class="n">18</span></li>
    <li class="sub">Chaise <span class="n">53</span></li>
    <li class="sub">Floor Lamps <span class="n">73</span></li>
    <li class="sub">Bath &amp; Vanity <span class="n">52</span></li>
    <li class="sub">Dinning Chairs <span class="n">11</span></li>
    <li class="sub">Dinning Tables <span class="n">7</span></li>
    <li class="top" style="margin-top:2px">BANGLES</li>
    <li class="top">PILLOS</li>
    <li class="top">STRING LIGHTS</li>
    <li class="top">LAMP SHADES</li>
    <li class="top">BUFFET SHADES</li>
    <li class="top">CUSHIONS</li>
  </ul>

  <div class="abs week">PRODUCT OF THE WEEK</div>
  <div class="abs week-img" role="img" aria-label="Pile of colourful woven cushions"></div>

  <div class="abs news-title">NEWS</div>
  <div class="abs news-sub">MEET OUR ARTISTIAN</div>
  <div class="abs news-item" style="top:650px">
    <div class="avatar" role="img" aria-label="Portrait of the featured artisan"></div>
    <div class="meta">24th Mar, 2014<br><span style="font-weight:700">Lorem Ispum is the dummy text.</span></div>
    <p>Lorem ipsum dolor sit amet, consectet adipisc eli lorem seder.Lorem ipsum is the dummy text of the industry</p>
  </div>
  <div class="abs news-item" style="top:744px">
    <div class="avatar" role="img" aria-label="Portrait of the featured artisan"></div>
    <div class="meta">24th Mar, 2014<br><span style="font-weight:700">Lorem Ispum is the dummy text.</span></div>
    <p>Lorem ipsum dolor sit amet, consectet adipisc eli seder.</p>
  </div>
  <div class="abs dots"><i></i><i class="on"></i><i></i><i></i><i></i></div>
  <div class="abs share">
    <span style="left:15px"></span><span style="left:52px"></span><span style="left:89px"></span>
  </div>
</aside>

<main>
  <div class="abs prod-search">SEARCH BANGLES
    <svg width="13" height="13" viewBox="0 0 13 13"><circle cx="5.5" cy="5.5" r="4.3" fill="none" stroke="#222" stroke-width="1.3"/><path d="M8.6 8.6 L12 12" stroke="#222" stroke-width="1.4"/></svg>
  </div>
  <svg class="abs" style="left:572px;top:143px" width="12" height="10" viewBox="0 0 12 10"><g fill="#222"><rect x="0" y="0" width="2" height="2"/><rect x="3" y="0" width="9" height="2"/><rect x="0" y="4" width="2" height="2"/><rect x="3" y="4" width="9" height="2"/><rect x="0" y="8" width="2" height="2"/><rect x="3" y="8" width="9" height="2"/></g></svg>
  <svg class="abs" style="left:598px;top:143px" width="10" height="10" viewBox="0 0 10 10"><g fill="#222"><rect x="0" y="0" width="2" height="2"/><rect x="4" y="0" width="2" height="2"/><rect x="8" y="0" width="2" height="2"/><rect x="0" y="4" width="2" height="2"/><rect x="4" y="4" width="2" height="2"/><rect x="8" y="4" width="2" height="2"/><rect x="0" y="8" width="2" height="2"/><rect x="4" y="8" width="2" height="2"/><rect x="8" y="8" width="2" height="2"/></g></svg>

  <div class="abs hero" role="img" aria-label="Featured product: red and cream woven wall plates on a dark background"></div>
  <div class="abs hero-dots"><i></i><i class="on"></i><i></i><i></i></div>

  <p class="abs statement">Our store carries modern African inspired items from designers that support social development and poverty alleviation initiatives.</p>

  <div class="abs section-label" style="top:488px">FEATURED PRODUCTS</div>
  <div class="abs section-label" style="top:667px">NEW PRODUCTS</div>

  <!-- featured row -->
  <div class="abs card" style="left:207px;top:518px"><div class="price">$ 144.00<svg width="11" height="8" viewBox="0 0 11 8"><path d="M0 1 H2 L3.5 6 H9 L10.5 2 H3" fill="none" stroke="#333"/><circle cx="4" cy="7.3" r=".7"/><circle cx="8.5" cy="7.3" r=".7"/></svg></div><div class="photo" role="img" aria-label="Woven multicoloured bowls" style="background:linear-gradient(160deg,#c9c9c9 30%,#b0705a 50%,#4a8a9a 60%,#c9c9c9 75%)"></div><div class="cap">LOREM IPSUM</div></div>
  <div class="abs card" style="left:306px;top:518px"><div class="price">$ 120.00<svg width="11" height="8" viewBox="0 0 11 8"><path d="M0 1 H2 L3.5 6 H9 L10.5 2 H3" fill="none" stroke="#333"/><circle cx="4" cy="7.3" r=".7"/><circle cx="8.5" cy="7.3" r=".7"/></svg></div><div class="photo" role="img" aria-label="Beaded zebra figurine" style="background:linear-gradient(180deg,#c9c9c9 15%,#8a8a8a 45%,#c9c9c9 80%)"></div><div class="cap">LOREM IPSUM</div></div>
  <div class="abs card" style="left:406px;top:518px"><div class="price">$ 125.00<svg width="11" height="8" viewBox="0 0 11 8"><path d="M0 1 H2 L3.5 6 H9 L10.5 2 H3" fill="none" stroke="#333"/><circle cx="4" cy="7.3" r=".7"/><circle cx="8.5" cy="7.3" r=".7"/></svg></div><div class="photo" role="img" aria-label="Striped woven basket in yellow and grey" style="background:linear-gradient(180deg,#c9c9c9 20%,#c9b23a 40%,#555 55%,#c9c9c9 80%)"></div><div class="cap">LOREM IPSUM</div></div>
  <div class="abs card" style="left:505px;top:518px"><div class="price">$ 130.00<svg width="11" height="8" viewBox="0 0 11 8"><path d="M0 1 H2 L3.5 6 H9 L10.5 2 H3" fill="none" stroke="#333"/><circle cx="4" cy="7.3" r=".7"/><circle cx="8.5" cy="7.3" r=".7"/></svg></div><div class="photo" role="img" aria-label="Carved wooden fish bowl" style="background:linear-gradient(180deg,#c9c9c9 35%,#9b5a33 50%,#c9c9c9 65%)"></div><div class="cap">LOREM IPSUM</div></div>

  <!-- new row -->
  <div class="abs card" style="left:207px;top:700px"><div class="price">$ 144.00<svg width="11" height="8" viewBox="0 0 11 8"><path d="M0 1 H2 L3.5 6 H9 L10.5 2 H3" fill="none" stroke="#333"/><circle cx="4" cy="7.3" r=".7"/><circle cx="8.5" cy="7.3" r=".7"/></svg></div><div class="photo" role="img" aria-label="Woven multicoloured bowls" style="background:linear-gradient(160deg,#c9c9c9 30%,#b0705a 50%,#4a8a9a 60%,#c9c9c9 75%)"></div><div class="cap">LOREM IPSUM</div></div>
  <div class="abs card" style="left:306px;top:700px"><div class="price">$ 120.00<svg width="11" height="8" viewBox="0 0 11 8"><path d="M0 1 H2 L3.5 6 H9 L10.5 2 H3" fill="none" stroke="#333"/><circle cx="4" cy="7.3" r=".7"/><circle cx="8.5" cy="7.3" r=".7"/></svg></div><div class="photo" role="img" aria-label="Beaded zebra figurine" style="background:linear-gradient(180deg,#c9c9c9 15%,#8a8a8a 45%,#c9c9c9 80%)"></div><div class="cap">LOREM IPSUM</div></div>
  <div class="abs card" style="left:406px;top:700px"><div class="price">$ 125.00<svg width="11" height="8" viewBox="0 0 11 8"><path d="M0 1 H2 L3.5 6 H9 L10.5 2 H3" fill="none" stroke="#333"/><circle cx="4" cy="7.3" r=".7"/><circle cx="8.5" cy="7.3" r=".7"/></svg></div><div class="photo" role="img" aria-label="Striped woven basket in yellow and grey" style="background:linear-gradient(180deg,#c9c9c9 20%,#c9b23a 40%,#555 55%,#c9c9c9 80%)"></div><div class="cap">LOREM IPSUM</div></div>
  <div class="abs card" style="left:505px;top:700px"><div class="price">$ 130.00<svg width="11" height="8" viewBox="0 0 11 8"><path d="M0 1 H2 L3.5 6 H9 L10.5 2 H3" fill="none" stroke="#333"/><circle cx="4" cy="7.3" r=".7"/><circle cx="8.5" cy="7.3" r=".7"/></svg></div><div class="photo" role="img" aria-label="Carved wooden fish bowl" style="background:linear-gradient(180deg,#c9c9c9 35%,#9b5a33 50%,#c9c9c9 65%)"></div><div class="cap">LOREM IPSUM</div></div>

  <div class="abs arrow" style="left:187px;top:585px"><svg width="12" height="12" viewBox="0 0 12 12"><path d="M7 3.5 L4.5 6 L7 8.5" fill="none" stroke="#fff" stroke-width="1.4"/></svg></div>
  <div class="abs arrow" style="left:603px;top:585px"><svg width="12" height="12" viewBox="0 0 12 12"><path d="M5 3.5 L7.5 6 L5 8.5" fill="none" stroke="#fff" stroke-width="1.4"/></svg></div>
  <div class="abs arrow" style="left:187px;top:767px"><svg width="12" height="12" viewBox="0 0 12 12"><path d="M7 3.5 L4.5 6 L7 8.5" fill="none" stroke="#fff" stroke-width="1.4"/></svg></div>
  <div class="abs arrow" style="left:603px;top:767px"><svg width="12" height="12" viewBox="0 0 12 12"><path d="M5 3.5 L7.5 6 L5 8.5" fill="none" stroke="#fff" stroke-width="1.4"/></svg></div>

  <div class="abs pager"><span>&#8249;</span><span class="on">1</span><span>2</span><span>3</span><span>4</span><span>&#8250;</span></div>
</main>

<!-- categories -->
<section>
  <h2 class="abs cat-title">CATEGORIES</h2>
  <div class="abs cat-rule"></div>
  <div class="abs chev" style="left:57px">&#8249;</div>
  <div class="abs chev" style="left:614px">&#8250;</div>
  <div class="abs chip" style="left:88px;top:931px">Cushions</div>
  <div class="abs chip" style="left:219px;top:931px">Bed Sheets</div>
  <div class="abs chip" style="left:351px;top:931px">Dinning Chairs</div>
  <div class="abs chip" style="left:483px;top:931px">Dinning Tables</div>
  <div class="abs chip" style="left:88px;top:965px">Decors</div>
  <div class="abs chip" style="left:219px;top:965px">Bangles</div>
  <div class="abs chip" style="left:351px;top:965px">String Lights</div>
  <div class="abs chip" style="left:483px;top:965px">Watches</div>
  <div class="abs chip" style="left:147px;top:998px">Jewelry</div>
  <div class="abs chip" style="left:279px;top:998px">Shoes</div>
  <div class="abs chip" style="left:411px;top:998px">Kitchen Items</div>
</section>

<!-- footer -->
<footer>
  <div class="abs footer"></div>
  <div class="abs brand fbrand"><span class="brand-mark"></span><div class="brand-name">AMARA HOME</div></div>

  <div class="abs fhead" style="left:205px">QUICK LINKS</div>
  <ul class="abs flinks">
    <li>Shop Now</li><li>Our Story</li><li>Blog</li><li>Custom Design</li><li>Our Shop</li><li>Press &amp; Mentions</li><li>Designer &amp; Architects</li><li>Video</li><li>Contact</li>
  </ul>

  <div class="abs fhead" style="left:336px">QUICK CONTACT</div>
  <div class="abs field" style="top:1074px">Name</div>
  <div class="abs field" style="top:1093px">Phone</div>
  <div class="abs field" style="top:1112px">Email</div>
  <div class="abs field" style="top:1131px;height:36px">Message</div>
  <div class="abs submit">Submit</div>

  <div class="abs fhead" style="left:530px">FOLLOW US</div>
  <div class="abs soc" style="left:520px;top:1074px"></div>
  <div class="abs soc" style="left:544px;top:1074px"></div>
  <div class="abs soc" style="left:568px;top:1074px"></div>
  <div class="abs soc" style="left:520px;top:1098px"></div>
  <div class="abs soc" style="left:544px;top:1098px"></div>
  <div class="abs soc" style="left:568px;top:1098px"></div>
  <div class="abs pay" style="left:499px;top:1130px"></div>
  <div class="abs pay" style="left:530px;top:1130px"></div>
  <div class="abs pay" style="left:560px;top:1130px"></div>
  <div class="abs pay" style="left:590px;top:1130px"></div>
  <div class="abs pay" style="left:509px;top:1154px;width:44px;height:12px"></div>
  <div class="abs pay" style="left:565px;top:1154px;width:36px;height:12px"></div>
  <div class="abs copy">© 2014 AmaraHome. All Rights Reserved</div>
</footer>

</body>
</html>
```